Business Cards for IT Consulting Company (Managed Service Provider)

I am looking to have some business cards printed and would like some designs. We are an IT Consulting company based in Vancouver BC. I would like a nice clean and modern look to the cards. I have uploaded all the versions of my logo so parts can be used as needed. Here is a snippit from our website homepage:

Quillbrook Networks Ltd. is an IT Solutions Partner located in Vancouver BC, Canada. We offer IT solutions and support to customers in the greater Vancouver Area. With expertise in Microsoft platforms, as well as Linux and Mac OSX and over 12 years experience in the IT industry, Quillbrook Networks is dedicated to offering our clients top quality service and products. We take pride in the solutions we offer our customers. The greatest compliment a client can give us is to recommend our services.

Quillbrook Networks Ltd. offers a wide range of IT services from onsite service to remote support and managed service solutions. This allows clients to choose the support path that best suits their company’s needs. Supporting many different sized companies from small to enterprise level over the past 12 years Quillbrook Networks has the experience and expertise needed to ensure things run smoothly. Allowing our clients to focus on doing business.

Rethinking How Your Business Technology Is Supported.

Quillbrook Networks is dedicated to providing our clients with IT solutions that work and grow with them for years to come. This philosophy helps save money in the long run instead of replacing equipment constantly. Far too often IT solutions are not well thought out and while possibly solving the problem at hand, require replacement due to growth or quality within a very short time frame. Quillbrook Networks takes pride in providing solutions that will last and be able to accommodate growth without the need for replacement.

Industry/Entity Type

Information Technology

Contact Information for Business Card

Quillbrook Networks Ltd.
(Employee Name)
Eml: (Employees Email Address)
Web: quillbrook.me
Ph: 604-555-0148

Font styles to use
Serif
Sans Serif

Requirements
Must have
• The Company logo and company colors.
Nice to have
• - Our tag line: "Revolutionizing IT Services" or "Rethinking How Your Business Technology Is Supported."
• - Also I really like the idea of nature and technology together blending which is sort of where my logo came from so integrating that somehow onto the business cards would be great.

```html
<!DOCTYPE html>
<html lang="en">
<head>
<meta charset="utf-8">
<title>Quillbrook Networks – Business Cards</title>
<link href="https://fonts.googleapis.com/css2?family=Open+Sans:wght@400;600;700&display=swap" rel="stylesheet">
<style>
  :root {
    --bg: #ece9e4;
    --card-white: #ffffff;
    --brand-blue: #1fa3dc;
    --brand-blue-deep: #0f94d0;
    --brand-blue-light: #3bb4e6;
    --ink: #5a5a5a;
    --ink-soft: #8a8a8a;
    --on-blue: #ffffff;
  }
  * { box-sizing: border-box; margin: 0; padding: 0; }
  html, body {
    width: 1200px; height: 1023px; overflow: hidden;
    background: var(--bg);
    font-family: "Open Sans", Arial, sans-serif;
  }
  .canvas { position: relative; width: 1200px; height: 1023px; }

  .card {
    position: absolute;
    border-radius: 4px;
    box-shadow: 0 6px 18px rgba(0,0,0,.18);
    overflow: hidden;
  }

  /* Front card */
  .card-front {
    left: 70px; top: 90px; width: 620px; height: 354px;
    background: var(--card-white);
  }
  .brand {
    position: absolute; left: 48px; top: 70px;
    display: flex; align-items: center; gap: 14px;
  }
  .brand-dot {
    width: 40px; height: 40px; border: 3px solid var(--brand-blue);
  }
  .brand-name {
    color: var(--brand-blue); font-weight: 700; font-size: 30px;
    line-height: 1.05; letter-spacing: -0.5px;
  }
  .person { position: absolute; left: 310px; top: 150px; }
  .person-name { font-size: 26px; font-weight: 600; color: var(--ink); }
  .person-name .first { color: var(--brand-blue); }
  .person-role { font-size: 14px; color: var(--ink-soft); margin-top: 2px; }
  .contact { list-style: none; margin-top: 26px; }
  .contact li {
    display: flex; align-items: center; gap: 9px;
    font-size: 15px; color: var(--ink); line-height: 26px;
  }
  .contact svg { width: 14px; height: 14px; fill: var(--brand-blue); flex: none; }

  /* Back card */
  .card-back {
    left: 760px; top: 360px; width: 354px; height: 620px;
    background: var(--brand-blue);
  }
  .pattern-field {
    position: absolute; inset: 0;
    background: linear-gradient(160deg, var(--brand-blue-light) 0%, var(--brand-blue) 50%, var(--brand-blue-deep) 100%);
  }
  .back-name {
    position: absolute; left: 0; right: 0; top: 290px;
    text-align: center; color: var(--on-blue);
    font-weight: 700; font-size: 26px; line-height: 1.15;
  }
  .tagline {
    position: absolute; left: 34px; top: 40px;
    transform-origin: left top; transform: rotate(90deg) translateY(-100%);
    white-space: nowrap; color: var(--on-blue);
    font-size: 14px; letter-spacing: 1.5px;
  }
</style>
</head>
<body>
<main class="canvas">
  <section class="card card-front" aria-label="Business card front">
    <div class="brand">
      <span class="brand-dot"></span>
      <span class="brand-name">Quillbrook<br>Networks Ltd.</span>
    </div>
    <div class="person">
      <p class="person-name"><span class="first">Employee</span> Name</p>
      <p class="person-role">Director</p>
      <ul class="contact">
        <li><svg viewBox="0 0 16 16"><path d="M3 1l3 3-2 2c1 2 3 4 5 5l2-2 3 3-2 3C6 15 1 10 1 3z"/></svg>604-555-0148</li>
        <li><svg viewBox="0 0 16 16"><path d="M1 3h14v10H1z M1 3l7 6 7-6" /></svg>Employees@quillbrooknetworks.com</li>
        <li><svg viewBox="0 0 16 16"><circle cx="8" cy="8" r="7"/></svg>www.quillbrooknetworks.com</li>
      </ul>
    </div>
  </section>

  <section class="card card-back" aria-label="Business card back">
    <div class="pattern-field" role="img" aria-label="Subtle tonal blue geometric pattern"></div>
    <p class="back-name">Quillbrook<br>Networks</p>
    <p class="tagline">Rethinking How Your Business Technology Is Supported.</p>
  </section>
</main>
</body>
</html>
```